Visitenkarten und Briefpapier
Zielgruppe
Planung und Realisierung von individuellen und wertbeständigen Kamin- und Ofenlösungen, sowie Fliesen- und Baddesign.
Aufgabenstellung
Wir benötigen ein möglichst schlichtes Design für Visitenkarten, bzw. Briefpapier. Für die Visitenkarten gerne auch Vorschläge mit Prägung, Ausstanzung oder mit Heißfolie. Auch Klappkarten wären denkbar. Das Design soll "das gewisse Etwas haben" und nicht zu verspielt sein.
Die Visitenkarten sind für die Firma KORVA, das Logo von der Ausstellung "raumfunke" soll dezent mit eingebunden werden (bei dem Briefpapier z.B. in der Fußzeile". Die farbliche Gestaltung sollte sich an den Farben des Logos orientieren.
Schriftart für Texte: Century Gothic
Schriftfarbe: RAL 7016
Nur eine Idee: Ich könnte mir auch gut vorstellen, dass die Visitenkarte aus einer Zündholzverpackung (wenn dann aber eine besondere mit nur einem Zündholz oder einem besonders breiten) besteht: http://glimmvelo.de/produkte_briefchen.php

```html
<!DOCTYPE html>
<html lang="de">
<head>
<meta charset="utf-8">
<title>KORVA – Visitenkarte</title>
<link rel="stylesheet" href="https://fonts.googleapis.com/css2?family=Questrial&display=swap">
<style>
  :root {
    --canvas: #e9e7e3;
    --card-dark: #1b252a;
    --card-light: #f3f3f2;
    --text-light: #d6d6d4;
    --text-ral7016: #383e42;
    --text-muted: #8b8d8f;
    --accent-flame: #d98021;
    --raumfunke-grey: #7d8488;
  }
  * { box-sizing: border-box; margin: 0; padding: 0; }
  html, body {
    width: 1200px; height: 840px; overflow: hidden;
    background: var(--canvas);
    font-family: "Questrial", "Century Gothic", sans-serif;
  }
  .canvas {
    position: relative; width: 1200px; height: 840px;
  }
  .card {
    position: absolute; top: 250px;
    width: 540px; height: 324px;
    box-shadow: 0 6px 18px rgba(0,0,0,.18);
  }
  /* Front */
  .card-front { left: 40px; background: var(--card-dark); color: var(--text-light); }
  .front-brand {
    position: absolute; left: 70px; top: 86px;
    display: flex; align-items: center; gap: 18px;
  }
  .front-brand .wordmark {
    font-size: 92px; letter-spacing: 6px; line-height: 1; color: var(--text-light);
  }
  .front-brand .brand-dot {
    width: 22px; height: 22px; border-radius: 50%; background: var(--accent-flame);
  }
  .front-tagline {
    position: absolute; left: 72px; top: 196px;
    font-size: 27px; letter-spacing: 1.5px; color: var(--text-light);
  }
  .front-partner {
    position: absolute; right: 30px; bottom: 24px;
    font-size: 20px; letter-spacing: 1px; color: var(--raumfunke-grey);
  }
  /* Back */
  .card-back { left: 620px; background: var(--card-light); color: var(--text-ral7016); }
  .back-brand {
    position: absolute; left: 34px; top: 24px;
  }
  .back-brand .wordmark-row { display: flex; align-items: center; gap: 10px; }
  .back-brand .wordmark { font-size: 44px; letter-spacing: 3px; line-height: 1; color: #1e2326; }
  .back-brand .brand-dot { width: 11px; height: 11px; border-radius: 50%; background: var(--accent-flame); }
  .back-brand .tagline { font-size: 13px; letter-spacing: .8px; margin-top: 4px; color: #1e2326; }
  .back-rule {
    position: absolute; left: 0; right: 0; top: 94px; height: 1.5px; background: var(--text-ral7016);
  }
  .address {
    position: absolute; left: 30px; top: 132px;
    display: flex; gap: 10px; font-size: 15px; line-height: 1.3; color: var(--text-muted);
  }
  .address svg { flex: none; margin-top: 2px; }
  .person {
    position: absolute; right: 30px; top: 150px; text-align: right;
  }
  .person .name {
    font-family: "Questrial", sans-serif; font-size: 22px; color: var(--text-ral7016);
    padding-bottom: 3px; border-bottom: 1.5px solid var(--text-ral7016);
  }
  .person .role { font-size: 13px; margin-top: 4px; color: var(--text-ral7016); }
  .contact {
    position: absolute; right: 30px; top: 222px; list-style: none;
  }
  .contact li {
    display: flex; justify-content: flex-end; align-items: center; gap: 12px;
    font-size: 15px; color: var(--text-muted); height: 26px;
  }
  .contact svg { width: 22px; height: 18px; fill: var(--text-ral7016); }
</style>
</head>
<body>
<main class="canvas">

  <section class="card card-front" aria-label="Visitenkarte Vorderseite">
    <div class="front-brand">
      <span class="wordmark">KORVA</span>
      <span class="brand-dot"></span>
    </div>
    <p class="front-tagline">kamine · öfen · fliesen</p>
    <p class="front-partner">raumfunke</p>
  </section>

  <section class="card card-back" aria-label="Visitenkarte Rückseite">
    <div class="back-brand">
      <div class="wordmark-row">
        <span class="wordmark">KORVA</span>
        <span class="brand-dot"></span>
      </div>
      <p class="tagline">kamine · öfen · fliesen</p>
    </div>
    <div class="back-rule"></div>

    <address class="address">
      <svg width="14" height="18" viewBox="0 0 14 18" aria-hidden="true">
        <path d="M7 0a7 7 0 0 0-7 7c0 5 7 11 7 11s7-6 7-11a7 7 0 0 0-7-7zm0 9.5A2.5 2.5 0 1 1 7 4.5a2.5 2.5 0 0 1 0 5z" fill="var(--text-ral7016)"/>
      </svg>
      <span>Am Lindenhang 12<br>34519 Talheim</span>
    </address>

    <div class="person">
      <p class="name">Jonas Wehrle</p>
      <p class="role">Geschäftsführer</p>
    </div>

    <ul class="contact">
      <li>05612 / 48 31 70
        <svg viewBox="0 0 22 18" aria-label="Telefon"><path d="M2 6c0-3 4-4 9-4s9 1 9 4v2h-5V6H7v2H2z"/><path d="M5 9h12l2 8H3z"/></svg>
      </li>
      <li>05612 / 48 31 79
        <svg viewBox="0 0 22 18" aria-label="Fax"><rect x="6" y="1" width="10" height="6"/><rect x="1" y="7" width="20" height="8" rx="1"/><rect x="5" y="13" width="12" height="4"/></svg>
      </li>
      <li>info@korva-talheim.de
        <svg viewBox="0 0 22 18" aria-label="E-Mail"><path d="M1 2h20v14H1z"/><path d="M2 3l9 7 9-7" fill="none" stroke="var(--card-light)" stroke-width="1.5"/></svg>
      </li>
    </ul>
  </section>

</main>
</body>
</html>
```